Business card por a urban DJ, up scale audience target

Need a sober design, modern, conservative colors but i can consider some options, y play rnb, hip hop, EDM and top40.

Business card for contact and personal info, double sided, use logo attrached please; im 42 so i need a card acording to my age an target audience.

Target Market(s)

Adult people, up scale audience

Industry/Entity Type

Music Download

Contact Information for Business Card

Cel (318) 4207265518 www.lumadrift.com

Requirements
Must have
• open mind
Nice to have
• open mind
Should not have
• DJ

```html
<!DOCTYPE html>
<html lang="en">
<head>
<meta charset="utf-8">
<title>Lumadrift Business Card</title>
<link href="https://fonts.googleapis.com/css2?family=Open+Sans:wght@400;600;800&display=swap" rel="stylesheet">
<style>
  :root {
    --bg: #e4e2e0;
    --card: #ffffff;
    --ink: #2b2a2a;
    --band: #3b393a;
    --band-edge: #111111;
    --light: #f2f2f2;
    --muted: #cfcfcf;
  }
  * { box-sizing: border-box; margin: 0; padding: 0; }
  html, body { width: 1200px; height: 780px; overflow: hidden; }
  body {
    background: var(--bg);
    font-family: "Open Sans", Arial, sans-serif;
    display: flex;
    align-items: center;
    justify-content: center;
    gap: 40px;
  }
  .card {
    position: relative;
    width: 540px;
    height: 310px;
    background: var(--card);
    box-shadow: 0 6px 18px rgba(0,0,0,0.18);
    overflow: hidden;
  }
  .brand-name {
    font-family: "Open Sans", Arial, sans-serif;
    font-weight: 800;
    color: var(--ink);
    letter-spacing: 2px;
    line-height: 1;
  }
  /* Front */
  .card-front {
    display: flex;
    flex-direction: column;
    align-items: center;
    justify-content: center;
  }
  .card-front .brand-name { font-size: 64px; margin-top: -10px; }
  .site-rule {
    display: flex;
    align-items: center;
    gap: 14px;
    margin-top: 34px;
  }
  .site-rule .rule { width: 70px; height: 1px; background: var(--ink); }
  .site-rule .site {
    font-family: Arial, sans-serif;
    font-weight: 700;
    font-size: 19px;
    color: var(--ink);
  }
  /* Back */
  .card-back .logo-area {
    height: 172px;
    display: flex;
    align-items: center;
    justify-content: center;
    padding-left: 120px;
  }
  .card-back .brand-name { font-size: 54px; }
  .card-back .edge { height: 10px; background: var(--band-edge); }
  .card-back .band {
    position: absolute;
    left: 0; right: 0; bottom: 0;
    top: 182px;
    background: var(--band);
    display: flex;
    justify-content: space-between;
    padding: 10px 20px 0 22px;
  }
  .person .name { color: var(--light); font-weight: 600; font-size: 17px; }
  .person .role { color: var(--muted); font-size: 15px; margin-top: 1px; }
  .contacts {
    list-style: none;
    border-left: 1px solid var(--light);
    padding: 10px 0 0 10px;
    margin-top: 28px;
    height: 88px;
  }
  .contacts li {
    display: flex;
    align-items: center;
    gap: 8px;
    color: var(--light);
    font-size: 13.5px;
    line-height: 19px;
  }
  .contacts svg { width: 11px; height: 11px; flex: none; }
</style>
</head>
<body>
  <section class="card card-front">
    <div class="brand-name">LUMADRIFT</div>
    <div class="site-rule">
      <span class="rule"></span>
      <span class="site">www.lumadrift.com</span>
      <span class="rule"></span>
    </div>
  </section>

  <section class="card card-back">
    <div class="logo-area"><div class="brand-name">LUMADRIFT</div></div>
    <div class="edge"></div>
    <div class="band">
      <div class="person">
        <div class="name">Daniel Whitcombe</div>
        <div class="role">Managing Director</div>
      </div>
      <ul class="contacts">
        <li>
          <svg viewBox="0 0 12 12"><rect width="12" height="12" fill="#f2f2f2"/><path d="M3 3h2l1 2-1 1a5 5 0 0 0 2 2l1-1 2 1v2h-1A7 7 0 0 1 3 4z" fill="#3b393a"/></svg>
          (318) 4207265518
        </li>
        <li>
          <svg viewBox="0 0 12 12"><rect width="12" height="12" fill="#f2f2f2"/><rect x="2" y="3.5" width="8" height="5" fill="none" stroke="#3b393a"/><path d="M2 3.5l4 3 4-3" fill="none" stroke="#3b393a"/></svg>
          info@lumadrift.com
        </li>
        <li>
          <svg viewBox="0 0 12 12"><rect width="12" height="12" fill="#f2f2f2"/><circle cx="6" cy="6" r="3.6" fill="none" stroke="#3b393a"/><path d="M2.4 6h7.2M6 2.4v7.2" stroke="#3b393a" stroke-width="0.8"/></svg>
          www.lumadrift.com
        </li>
        <li>
          <svg viewBox="0 0 12 12"><rect width="12" height="12" fill="#f2f2f2"/><path d="M6 10.5L3.3 6.2a3 3 0 1 1 5.4 0z" fill="#3b393a"/><circle cx="6" cy="4.6" r="1" fill="#f2f2f2"/></svg>
          418 Harbor View Ln, Portland ME 041
        </li>
      </ul>
    </div>
  </section>
</body>
</html>
```